Business Card Design needed - Something Awesome!

Need a business card designed. Company is "Marlowe Advisory" we do consulting and also have sales automation technology.
I'm going to use thick stock or metal, something really nice... I was thinking about a QR Code on the back that would just upload my contact info to the persons contact, etc -

This is a Strategy Company with a tech feel. I'm open to ideas but really want this to be nice!

I need a template that should include:

Name | Position or Title
D: 415.902.3376
www.marloweadvisory.example

I'm going to attach my contact so you can use that one, I need to get this printed.

Target Market(s)

Small to mid size customers, Entrepreneurs etc.

Industry/Entity Type

Consulting, Tech, Private Equity.

Contact Information for Business Card

Name, Phone, Maybe email, URL

Font styles to use
Sans Serif

Colors

Designer to choose only greyscale colors for use in the design.

Requirements
Must have
• Fresh, Clean, stand out from the crowd - will be on thick stock or metal.
Nice to have
• Clean, simple yet impactful.
Should not have
• Not cartoonish

```html
<!DOCTYPE html>
<html lang="en">
<head>
<meta charset="utf-8">
<title>Marlowe Advisory – Business Card</title>
<link href="https://fonts.googleapis.com/css2?family=Roboto:wght@300;400;500;700&display=swap" rel="stylesheet">
<style>
  :root {
    --surface: #3b3b3b;
    --card: #111111;
    --silver: #d6d6d6;
    --silver-soft: #a9a9a9;
    --muted: #8c8c8c;
    --rule: #9a9a9a;
    --gloss: #1d1d1d;
  }
  * { margin: 0; padding: 0; box-sizing: border-box; }
  html, body {
    width: 1200px; height: 801px; overflow: hidden;
    background: var(--surface);
    font-family: "Roboto", Arial, sans-serif;
  }
  .stage {
    position: relative; width: 1200px; height: 801px;
    display: flex; align-items: center; justify-content: center; gap: 60px;
  }
  .card {
    position: relative; width: 520px; height: 297px;
    background: var(--card);
    box-shadow: 0 18px 40px rgba(0,0,0,.45);
    overflow: hidden;
  }
  /* front */
  .wordmark {
    position: absolute; right: 36px; top: 34px;
    display: flex; align-items: center; gap: 10px;
    font-weight: 500; font-size: 40px; letter-spacing: 2px;
    color: var(--silver);
  }
  .wordmark .mark-square { width: 14px; height: 14px; background: var(--silver); }
  .divider {
    position: absolute; left: 36px; right: 36px; top: 150px;
    height: 1px; background: var(--rule);
  }
  .identity { position: absolute; left: 36px; top: 104px; }
  .identity .name {
    font-weight: 700; font-size: 17px; letter-spacing: .5px;
    color: var(--silver);
  }
  .identity .title { font-size: 13px; color: var(--muted); margin-top: 4px; font-weight: 300; }
  .contacts { position: absolute; left: 36px; top: 166px; list-style: none; }
  .contacts li {
    display: flex; align-items: center; gap: 8px;
    font-size: 13px; color: var(--silver-soft); margin-bottom: 6px;
  }
  .contacts svg { width: 11px; height: 11px; fill: var(--silver-soft); }
  .website {
    position: absolute; right: 36px; bottom: 40px;
    font-size: 12px; color: var(--silver-soft); letter-spacing: .3px;
  }
  .foil-bar {
    position: absolute; right: 0; bottom: 0; width: 190px; height: 10px;
    background: linear-gradient(90deg, #6e6e6e, #e4e4e4 45%, #9c9c9c);
  }
  /* back */
  .card-back { display: flex; align-items: center; justify-content: center; }
  .back-wordmark {
    display: flex; align-items: center; gap: 14px;
    font-weight: 500; font-size: 58px; letter-spacing: 3px;
    color: var(--silver-soft);
  }
  .back-wordmark .mark-square { width: 20px; height: 20px; background: var(--silver-soft); }
</style>
</head>
<body>
<main class="stage">
  <section class="card card-front" aria-label="Business card front">
    <div class="wordmark"><span>MARLOWE</span><span class="mark-square"></span></div>
    <div class="identity">
      <p class="name">JULIAN R. HASKELL</p>
      <p class="title">Founder / CEO</p>
    </div>
    <div class="divider"></div>
    <ul class="contacts">
      <li>
        <svg viewBox="0 0 24 24"><path d="M6.6 10.8a15.1 15.1 0 0 0 6.6 6.6l2.2-2.2c.3-.3.7-.4 1-.2 1.1.4 2.3.6 3.6.6.6 0 1 .4 1 1V20c0 .6-.4 1-1 1A17 17 0 0 1 3 4c0-.6.4-1 1-1h3.5c.6 0 1 .4 1 1 0 1.3.2 2.5.6 3.6.1.3 0 .7-.2 1z"/></svg>
        415.902.3376
      </li>
      <li>
        <svg viewBox="0 0 24 24"><path d="M2 5h20v14H2zm2 2v.5l8 5 8-5V7z"/></svg>
        info@marloweadvisory.example
      </li>
    </ul>
    <p class="website">www.marloweadvisory.example</p>
    <div class="foil-bar"></div>
  </section>

  <section class="card card-back" aria-label="Business card back">
    <div class="back-wordmark"><span>MARLOWE</span><span class="mark-square"></span></div>
  </section>
</main>
</body>
</html>
```